Meridian Vault Data Works Needs a Website Desing

We need a website design for a new company based in Kuwait called Meridian Vault Data Works (MVDW). We provide Software as a Service (SaaS) solutions for small and medium business companies. We will develop the required E-systems like HR,Payroll,Accounting Systems for those customers who wants to focus on their business instead of wasting time to automate it. MVDW need a web site that represent this activity and showing our cloud products and allow out customers to easily identify their needs. as a normal web site basic things need to be included like :
about MVDW
Solutions
PressRoom
Contact us
please i need something similar to tralvex.com or ozk.com or www.plorvane.com with blue and black theme .. please check the Company's logo
hi all ,,,
the project is only design without any codes
Reason: The project is focus on design only ,, i will be really appreciated to have more designs

```html
<!DOCTYPE html>
<html lang="en">
<head>
<meta charset="utf-8">
<title>Meridian Vault Data Works</title>
<link rel="stylesheet" href="https://fonts.googleapis.com/css2?family=Audiowide&family=Cinzel:wght@400;700&family=PT+Sans:wght@400;700&family=Tinos&display=swap">
<style>
  :root {
    --page-dark: #101214;
    --white: #ffffff;
    --ink: #111111;
    --ink-soft: #333333;
    --cyan: #4fd6f0;
    --cyan-light: #bff3f8;
    --cloud-top: #dff6ff;
    --cloud-bottom: #4aa8ea;
    --hero-deep: #04123a;
    --hero-mid: #0b3fa0;
    --hero-glow: #2f86e6;
  }
  * { box-sizing: border-box; margin: 0; padding: 0; }
  html, body { width: 1200px; height: 1000px; overflow: hidden; }
  body {
    position: relative;
    background: var(--page-dark);
    font-family: "PT Sans", sans-serif;
  }
  .header {
    position: absolute; left: 0; top: 25px; width: 1200px; height: 150px;
    background: var(--white);
  }
  .brand { position: absolute; left: 35px; top: 45px; display: flex; align-items: center; gap: 14px; }
  .brand-mark { width: 92px; height: 92px; border-radius: 50%; background: var(--cloud-bottom); }
  .brand-text { display: flex; flex-direction: column; }
  .brand-name { font-weight: 700; font-size: 84px; line-height: 70px; color: var(--ink); letter-spacing: 10px; }
  .brand-tagline { font-weight: 700; font-size: 16px; letter-spacing: 3.5px; color: var(--ink); margin-top: 2px; white-space: nowrap; }
  .social-area {
    position: absolute; left: 697px; top: 5px; width: 310px; height: 120px;
    border-radius: 60px 60px 20px 20px;
    background: linear-gradient(var(--cloud-top), var(--cloud-bottom));
  }
  .social-links {
    position: absolute; left: 768px; top: 98px; display: flex; gap: 10px;
  }
  .social-links a {
    display: flex; align-items: center; gap: 3px;
    font-size: 13px; font-weight: 700;
    color: var(--ink); text-decoration: none;
  }
  .social-links a::before {
    content: ""; width: 12px; height: 12px; border-radius: 2px; background: var(--white);
  }
  .account-links {
    position: absolute; left: 1035px; top: 32px; width: 150px;
    font-family: "Cinzel", serif; font-size: 25px; line-height: 36px; color: var(--ink-soft); text-align: center;
  }
  .search-field {
    position: absolute; left: 686px; top: 148px; width: 345px; height: 36px;
    background: var(--white); border: 3px solid var(--ink); border-radius: 8px;
  }
  .search-button {
    position: absolute; left: 1037px; top: 148px; width: 154px; height: 36px;
    background: var(--cyan-light); border: 3px solid var(--ink); border-radius: 8px;
    font-family: "Cinzel", serif; font-size: 23px; color: var(--ink);
    display: flex; align-items: center; justify-content: center; gap: 4px;
  }
  .main-nav {
    position: absolute; left: 5px; top: 196px; width: 1190px; height: 52px;
    background: linear-gradient(#e6fbfd, var(--cyan-light) 60%, #9fe6ef);
    border-radius: 8px; box-shadow: 0 3px 6px rgba(0,0,0,.5);
    display: flex; align-items: center; justify-content: space-between; padding: 0 42px;
    font-size: 30px; color: var(--ink);
  }
  .main-nav .dot { font-size: 20px; }
  .hero {
    position: absolute; left: 14px; top: 254px; width: 1172px; height: 338px;
    background: radial-gradient(ellipse at 85% 30%, var(--hero-glow), transparent 45%),
                linear-gradient(170deg, var(--hero-deep) 0%, var(--hero-mid) 55%, var(--hero-glow) 78%, var(--hero-deep) 100%);
    border: 1px solid #2a3a55;
  }
  .hero-title {
    position: absolute; left: 62px; top: 26px;
    font-family: "Audiowide", sans-serif; font-style: italic; font-size: 48px; letter-spacing: 3px;
    color: var(--cyan-light); text-shadow: 0 3px 4px rgba(0,0,0,.6);
  }
  .hero-subtitle {
    position: absolute; left: 146px; top: 100px; white-space: nowrap;
    font-family: "Audiowide", sans-serif; font-style: italic; font-size: 30px; letter-spacing: 4px;
    color: var(--cyan-light); text-transform: lowercase;
  }
  .team-photo {
    position: absolute; left: 0; top: 620px; width: 215px; height: 335px;
    background: linear-gradient(#3a2a22, #2b2b2e 40%, #1c1d20);
    border-radius: 90px 90px 0 0;
  }
  .services-frame {
    position: absolute; left: 228px; top: 612px; width: 964px; height: 346px;
    border: 3px solid var(--cyan); border-radius: 10px;
    box-shadow: 0 0 8px var(--cyan), inset 0 0 6px rgba(79,214,240,.4);
  }
  .service { position: absolute; top: 622px; width: 170px; height: 100px; }
  .service-art {
    position: absolute; inset: 0; border-radius: 50px 50px 24px 24px;
    background: linear-gradient(var(--cloud-top), var(--cloud-bottom));
  }
  .service span {
    position: absolute; left: 0; right: 0; top: 64px; text-align: center;
    font-family: "Tinos", serif; font-size: 9px; color: var(--white); text-transform: uppercase;
  }
  .service::after {
    content: ""; position: absolute; left: 38px; width: 94px; top: 122px; height: 4px;
    background: #d8dadc; border-radius: 50%;
  }
  .about-box {
    position: absolute; left: 248px; top: 765px; width: 924px; height: 180px;
    border: 3px solid var(--cyan); border-radius: 6px;
    box-shadow: 0 0 6px var(--cyan);
  }
  .about-visual {
    position: absolute; left: 272px; top: 780px; width: 195px; height: 146px;
    background: linear-gradient(#f7fbfd, #dfeef4);
  }
  .about-text {
    position: absolute; left: 478px; top: 791px; white-space: nowrap;
    font-family: "Tinos", serif; font-size: 22px; line-height: 30px; color: var(--cyan);
  }
  .footer-copy {
    position: absolute; left: 28px; top: 968px;
    font-family: "Cinzel", serif; font-size: 17px; font-weight: 700; color: var(--cyan-light);
  }
  .footer-links {
    position: absolute; right: 46px; top: 968px; width: 525px; text-align: right; white-space: nowrap;
    font-family: "Cinzel", serif; font-size: 17px; color: var(--cyan-light);
  }
</style>
</head>
<body>
  <header class="header">
    <div class="brand">
      <div class="brand-mark"></div>
      <div class="brand-text">
        <span class="brand-name">MVDW</span>
        <span class="brand-tagline">Meridian Vault Data Works</span>
      </div>
    </div>
    <div class="social-area" role="img" aria-label="Decorative light blue cloud illustration behind the social links"></div>
    <div class="account-links">
      <div>LOGIN</div>
      <div>REGISTER</div>
    </div>
  </header>
  <nav class="social-links">
    <a href="#">Friendline</a>
    <a href="#">Chirpwave</a>
    <a href="#">Newsrill</a>
  </nav>

  <div class="search-field"></div>
  <div class="search-button">SEARCH
    <svg width="20" height="20" viewBox="0 0 20 20"><circle cx="8" cy="8" r="6" fill="none" stroke="#111" stroke-width="2.5"/><line x1="12.5" y1="12.5" x2="18" y2="18" stroke="#111" stroke-width="3"/></svg>
  </div>

  <nav class="main-nav">
    <span>HOME</span><span class="dot">•</span>
    <span>ABOUT US</span><span class="dot">•</span>
    <span>SOLUTIONS</span><span class="dot">•</span>
    <span>PRODUCTS</span><span class="dot">•</span>
    <span>PRESS ROOM</span><span class="dot">•</span>
    <span>CAREERS</span>
  </nav>

  <section class="hero" role="img" aria-label="Abstract blue light waves with glowing particles">
    <h1 class="hero-title">BEST SOLUTIONS</h1>
    <p class="hero-subtitle">for small and medium business companies</p>
  </section>

  <div class="team-photo" role="img" aria-label="Photo of a smiling businesswoman in a dark suit with arms crossed"></div>

  <div class="services-frame"></div>
  <div class="service" style="left:290px"><div class="service-art" role="img" aria-label="Decorative cloud illustration"></div><span>Cloud Services</span></div>
  <div class="service" style="left:510px"><div class="service-art" role="img" aria-label="Decorative cloud illustration"></div><span>Virtualisation</span></div>
  <div class="service" style="left:730px"><div class="service-art" role="img" aria-label="Decorative cloud illustration"></div><span>Company</span></div>
  <div class="service" style="left:952px"><div class="service-art" role="img" aria-label="Decorative cloud illustration"></div><span>Support &amp;Downloads</span></div>

  <div class="about-box"></div>
  <div class="about-visual" role="img" aria-label="Illustration of laptops, monitors and phones connected to a cloud"></div>
  <p class="about-text">We provide Software as a Service (SaaS) solutions for small and<br>medium business companies. We will develop the required E-systems<br>like HR,Payroll,Accounting Systems for those customers who wants<br>to focus on their business instead of wasting time to automate it.</p>

  <footer>
    <div class="footer-copy">© COPYRIGHT 2013,MVDW,INC. ALL RIGHTS RESERVED</div>
    <div class="footer-links">CONTACT US •TERMS OF USE •PRIVACY •HELP •FEEDBACK</div>
  </footer>
</body>
</html>
```